Slide Master for Holloway Engines - A Systematic Hedge Fund

We are looking for someone to produce a theme and slide master for us for our investor presentations. I have uploaded a few examples of templates that we would like to have included:
Main Title
Section Title
Slides with just bullet points
Different image/table configurations with bullet points and foot notes
Biographies of different lengths
A disclaimer (no one will read this but it should still look nice and needs to be in the presentations)
I have also uploaded the company logo, business card and colour definitions. Currently we have a blue colour scheme defined, but it would be nice to get a complementary set of colours so that when we have charts with more elements we can just draw from those.
The most important thing is that the slide master must be of general use to us. We arn't looking to have a specific presentation designed for us, but a theme/style that we can apply ourselves to any presentation we need to give in the future. It should have clearly defined guidelines for where content should go (and if this is different with and without footnotes for example). We would also like it to have a similar feel to the logo/business cards, so matt colours, high contrast, but not busy.
I'm excited to see the results!

```html
<!DOCTYPE html>
<html lang="en">
<head>
<meta charset="utf-8">
<title>Holloway Engines – Slide Master</title>
<link href="https://fonts.googleapis.com/css2?family=Montserrat:wght@400;500;600;700;800&display=swap" rel="stylesheet">
<style>
:root{
  --navy:#103f7a;
  --blue:#2f6fb8;
  --sky:#6aa6e0;
  --pale:#c7dcf2;
  --mist:#e8f0f9;
  --ink:#24282e;
  --body:#555c66;
  --grey:#8a9099;
  --line:#dde2e8;
  --stage:#eef1f5;
  --white:#ffffff;
}
*{box-sizing:border-box;margin:0;padding:0}
html,body{width:1200px;height:3997px;overflow:hidden}
body{background:var(--white);font-family:"Montserrat",Arial,sans-serif;color:var(--ink);position:relative}

.stage{position:absolute;left:0;top:0;width:1200px;height:1190px;background:var(--stage)}
.cover{position:absolute;left:180px;top:250px;width:840px;height:472px;background:var(--navy);
  display:flex;align-items:center;justify-content:center;box-shadow:0 18px 40px rgba(16,63,122,.25)}
.cover .brand{font-size:54px}
.cover::after{content:"";position:absolute;left:0;right:0;bottom:0;height:8px;background:var(--blue)}

.brand{font-weight:800;color:var(--navy);text-align:center;line-height:1.05;letter-spacing:.06em;text-transform:uppercase}
.brand.on-dark{color:var(--white)}
.brand.lg{font-size:20px}
.brand.md{font-size:15px}

.deck{position:absolute;left:15px;top:1218px;width:1169px;display:grid;grid-template-columns:repeat(3,379px);
  column-gap:16px;row-gap:19px}
.slide{position:relative;width:379px;height:212px;background:var(--white);overflow:hidden;
  box-shadow:0 1px 5px rgba(0,0,0,.14)}
.slide.dark{background:var(--navy)}
.slide::after{content:"";position:absolute;left:0;right:0;bottom:0;height:3px;background:var(--navy)}
.slide.dark::after{background:var(--blue)}
.head{position:absolute;left:14px;top:10px;font-size:12px;font-weight:700;color:var(--navy)}
.head em{font-style:normal;color:var(--blue)}
.sub{position:absolute;left:14px;top:26px;font-size:5px;color:var(--blue);font-weight:600}
.mark{position:absolute;right:12px;top:9px;font-size:6.5px;font-weight:800;color:var(--navy);text-align:center;line-height:1.1;letter-spacing:.05em}
.foot{position:absolute;left:14px;right:14px;bottom:7px;display:flex;justify-content:space-between;font-size:4.2px;color:var(--grey);font-weight:600}
.tx{font-size:5px;line-height:1.45;color:var(--body)}
.tt{font-size:6px;font-weight:700;color:var(--navy);margin-bottom:1px}
.tt.b{color:var(--blue)}
.abs{position:absolute}
.photo{background:linear-gradient(135deg,#b9c4cf,#6f7f91)}
.photo.warm{background:linear-gradient(135deg,#d8c8ba,#8b7a6d)}
.photo.desk{background:linear-gradient(135deg,#d9dde2,#3e4b5a)}
.net{background:radial-gradient(circle at 72% 38%,rgba(47,111,184,.28),rgba(47,111,184,0) 45%),
  radial-gradient(circle at 88% 78%,rgba(106,166,224,.3),rgba(106,166,224,0) 40%)}
.net.dark{background:radial-gradient(circle at 72% 38%,rgba(106,166,224,.5),rgba(16,63,122,0) 48%),
  radial-gradient(circle at 90% 85%,rgba(106,166,224,.4),rgba(16,63,122,0) 40%)}
.pill{display:inline-block;border:1px solid var(--navy);border-radius:8px;padding:2px 8px;font-size:4.5px;font-weight:700;color:var(--navy);letter-spacing:.1em}
.num{font-weight:300;color:var(--pale);line-height:1}
.dot{display:inline-block;width:6px;height:6px;border-radius:50%;background:var(--navy);margin-right:2px}
.vurl{position:absolute;font-size:4px;letter-spacing:1.5px;color:var(--grey);transform:rotate(90deg);transform-origin:left top;white-space:nowrap}
.stack{display:flex;flex-direction:column}
</style>
</head>
<body>

<section class="stage">
  <div class="cover">
    <div class="brand on-dark">Holloway<br>Engines</div>
  </div>
</section>

<main class="deck">

  <article class="slide">
    <div class="brand lg abs" style="left:0;right:0;top:82px">Holloway<br>Engines</div>
    <div class="vurl" style="left:362px;top:50px">WWW.HOLLOWAYENGINES.COM</div>
  </article>

  <article class="slide">
    <div class="brand md abs" style="left:30px;top:88px">Holloway<br>Engines</div>
    <div class="abs" style="left:198px;top:30px;width:1px;height:150px;background:var(--line)"></div>
    <div class="abs" style="left:206px;top:34px;font-size:13px;font-weight:700;line-height:1.15;color:var(--navy)">HOLLOWAY<br><span style="color:var(--sky)">ENGINES</span><br>PRESENTATION</div>
    <div class="abs" style="left:206px;top:84px;font-size:4.2px;letter-spacing:2px;color:var(--grey)">SUBTITLE GOES HERE</div>
    <div class="abs" style="left:206px;top:116px;font-size:4.5px;color:var(--ink);font-weight:600">Month 2021</div>
    <div class="abs" style="left:206px;top:142px"><span class="pill">PRESENTER NAME</span></div>
  </article>

  <article class="slide">
    <div class="mark" style="left:0;right:0;top:16px">HOLLOWAY<br>ENGINES</div>
    <div class="abs net dark" role="img" aria-label="Connected network lines on deep blue" style="left:0;right:0;top:48px;bottom:0;background-color:var(--navy)"></div>
    <div class="abs" style="left:0;right:0;top:66px;text-align:center;color:var(--pale);font-size:4.2px;letter-spacing:2px">WWW.HOLLOWAYENGINES.COM</div>
    <div class="abs" style="left:0;right:0;top:82px;text-align:center;color:var(--white);font-size:13px;font-weight:700">MASTER SLIDE PRESENTATION</div>
    <div class="abs" style="left:0;right:0;top:102px;text-align:center;color:var(--pale);font-size:4.2px;letter-spacing:2px">SUBTITLE GOES HERE</div>
    <div class="abs" style="left:0;right:0;top:130px;text-align:center;color:var(--white);font-size:4.5px">Month 2021</div>
    <div class="abs" style="left:0;right:0;top:148px;text-align:center;color:var(--white);font-size:4.5px;letter-spacing:1.5px;font-weight:600">PRESENTER NAME</div>
  </article>

  <article class="slide dark">
    <div class="brand lg on-dark abs" style="left:0;right:0;top:82px">Holloway<br>Engines</div>
    <div class="vurl" style="left:364px;top:50px;color:var(--pale)">WWW.HOLLOWAYENGINES.COM</div>
  </article>

  <article class="slide">
    <div class="abs net" role="img" aria-label="Faint network lines" style="inset:0"></div>
    <div class="brand lg abs" style="left:0;right:0;top:82px;color:#16202c">Holloway<br>Engines</div>
    <div class="vurl" style="left:362px;top:50px">WWW.HOLLOWAYENGINES.COM</div>
  </article>

  <article class="slide">
    <div class="head">Table Of Content/Agenda</div>
    <div class="mark">HOLLOWAY<br>ENGINES</div>
    <div class="abs" style="left:30px;top:44px;display:grid;grid-template-columns:160px 160px;row-gap:12px;column-gap:30px">
      <div style="display:flex;gap:7px"><span class="num" style="font-size:28px">1</span><div><div class="tt" style="color:var(--ink)">Content here</div><div class="tx">Add a short line of text here to explain this point.</div></div></div>
      <div style="display:flex;gap:7px"><span class="num" style="font-size:28px">4</span><div><div class="tt" style="color:var(--ink)">Content here</div><div class="tx">Add a short line of text here to explain this point.</div></div></div>
      <div style="display:flex;gap:7px"><span class="num" style="font-size:28px">2</span><div><div class="tt" style="color:var(--ink)">Content here</div><div class="tx">Add a short line of text here to explain this point.</div></div></div>
      <div style="display:flex;gap:7px"><span class="num" style="font-size:28px">5</span><div><div class="tt" style="color:var(--ink)">Content here</div><div class="tx">Add a short line of text here to explain this point.</div></div></div>
      <div style="display:flex;gap:7px"><span class="num" style="font-size:28px">3</span><div><div class="tt" style="color:var(--ink)">Content here</div><div class="tx">Add a short line of text here to explain this point.</div></div></div>
      <div style="display:flex;gap:7px"><span class="num" style="font-size:28px">6</span><div><div class="tt" style="color:var(--ink)">Content here</div><div class="tx">Add a short line of text here to explain this point.</div></div></div>
    </div>
    <div class="foot"><span>HOLLOWAY ENGINES | 2021</span><span>PAGE | 4</span></div>
  </article>

  <article class="slide">
    <div class="abs net" role="img" aria-label="Network of connected points on the right" style="left:150px;right:0;top:0;bottom:0"></div>
    <div class="mark" style="left:20px;right:auto;top:34px;text-align:left;font-size:8px">HOLLOWAY<br>ENGINES</div>
    <div class="abs" style="left:20px;top:98px;font-size:13px;font-weight:700;color:var(--navy);line-height:1.15">MASTER SLIDE<br>PRESENTATION</div>
    <div class="abs" style="left:20px;top:133px;font-size:4.2px;letter-spacing:2px;color:var(--grey)">SUBTITLE GOES HERE</div>
    <div class="abs" style="left:20px;top:148px"><span class="dot"></span><span class="dot"></span><span class="dot"></span></div>
  </article>

  <article class="slide dark">
    <div class="abs net dark" role="img" aria-label="Network of connected points on the right" style="left:150px;right:0;top:0;bottom:0"></div>
    <div class="mark" style="left:20px;right:auto;top:34px;text-align:left;font-size:8px;color:var(--white)">HOLLOWAY<br>ENGINES</div>
    <div class="abs" style="left:20px;top:98px;font-size:13px;font-weight:700;color:var(--white);line-height:1.15">MASTER SLIDE<br>PRESENTATION</div>
    <div class="abs" style="left:20px;top:133px;font-size:4.2px;letter-spacing:2px;color:var(--pale)">SUBTITLE GOES HERE</div>
    <div class="abs" style="left:20px;top:148px"><span class="dot" style="background:var(--white)"></span><span class="dot" style="background:var(--white)"></span><span class="dot" style="background:var(--white)"></span></div>
  </article>

  <article class="slide">
    <div class="head">Introduction</div>
    <div class="mark">HOLLOWAY<br>ENGINES</div>
    <svg class="abs" style="left:34px;top:82px" width="36" height="36" viewBox="0 0 36 36"><circle cx="18" cy="18" r="17" fill="var(--mist)"/><text x="18" y="30" text-anchor="middle" font-size="28" font-weight="800" fill="var(--blue)" font-family="Montserrat">”</text></svg>
    <div class="abs tx" style="left:120px;top:72px;width:240px">Use this space for a short opening note that sets out the aim of the talk and the main idea you want people to keep in mind. Add one more line to frame what follows and why it matters to the reader.</div>
    <div class="abs tx" style="left:280px;top:120px;color:var(--ink);font-weight:600">– Name here/ Manager</div>
    <div class="foot"><span>HOLLOWAY ENGINES | 2021</span><span>PAGE | 5</span></div>
  </article>

  <article class="slide">
    <div class="head">Timeline</div>
    <div class="mark">HOLLOWAY<br>ENGINES</div>
    <svg class="abs" style="left:14px;top:40px" width="350" height="140" viewBox="0 0 350 140">
      <line x1="40" y1="70" x2="318" y2="70" stroke="var(--line)" stroke-width="2"/>
      <g fill="var(--pale)"><circle cx="80" cy="70" r="6"/><circle cx="118" cy="70" r="6"/><circle cx="156" cy="70" r="6"/><circle cx="194" cy="70" r="6"/><circle cx="232" cy="70" r="6"/><circle cx="270" cy="70" r="6"/></g>
      <circle cx="318" cy="70" r="12" fill="var(--navy)"/>
      <text x="318" y="72" text-anchor="middle" font-size="5.5" fill="#fff" font-weight="700" font-family="Montserrat">2021</text>
      <g font-size="4.6" fill="var(--ink)" font-family="Montserrat" text-anchor="middle">
        <text x="80" y="60">2013</text><text x="118" y="86">2014</text><text x="156" y="60">2015</text><text x="194" y="86">2016</text><text x="232" y="60">2017</text><text x="270" y="86">2018</text>
        <text x="80" y="26" font-weight="700">Contents</text><text x="80" y="33" fill="var(--body)">Short note</text><text x="80" y="39" fill="var(--body)">on this step.</text>
        <text x="156" y="26" font-weight="700">Contents</text><text x="156" y="33" fill="var(--body)">Short note</text><text x="156" y="39" fill="var(--body)">on this step.</text>
        <text x="232" y="26" font-weight="700">Contents</text><text x="232" y="33" fill="var(--body)">Short note</text><text x="232" y="39" fill="var(--body)">on this step.</text>
        <text x="118" y="102" font-weight="700">Contents</text><text x="118" y="109" fill="var(--body)">Short note</text><text x="118" y="115" fill="var(--body)">on this step.</text>
        <text x="194" y="102" font-weight="700">Contents</text><text x="194" y="109" fill="var(--body)">Short note</text><text x="194" y="115" fill="var(--body)">on this step.</text>
        <text x="270" y="102" font-weight="700">Contents</text><text x="270" y="109" fill="var(--body)">Short note</text><text x="270" y="115" fill="var(--body)">on this step.</text>
        <text x="318" y="96" font-weight="700">Objective</text><text x="318" y="103" fill="var(--body)">Short note</text><text x="318" y="109" fill="var(--body)">on the goal.</text>
      </g>
      <text x="2" y="68" font-size="8" font-weight="700" fill="var(--ink)" font-family="Montserrat">Start</text>
      <text x="2" y="76" font-size="4.6" fill="var(--body)" font-family="Montserrat">Contents</text>
      <text x="306" y="48" font-size="8" font-weight="700" fill="var(--ink)" font-family="Montserrat">Vision</text>
    </svg>
    <div class="foot"><span>HOLLOWAY ENGINES | 2021</span><span>PAGE | 6</span></div>
  </article>

  <article class="slide">
    <div class="head">Your Title Here - One Column</div>
    <div class="mark">HOLLOWAY<br>ENGINES</div>
    <div class="brand abs" style="right:36px;top:92px;font-size:15px;color:var(--line)">Holloway<br>Engines</div>
    <div class="abs tt" style="left:14px;top:50px;color:var(--ink)">Introduction</div>
    <div class="abs tx" style="left:14px;top:62px;width:170px">Use this column for the main text of the slide. Keep each line short and clear so the point is easy to follow. Add a second sentence to give more detail and a third one to close the thought with care. A final line can point to the next slide.</div>
    <div class="foot"><span>HOLLOWAY ENGINES | 2021</span><span>PAGE | 7</span></div>
  </article>

  <article class="slide">
    <div class="head">Your Title Here - Two Column</div>
    <div class="mark">HOLLOWAY<br>ENGINES</div>
    <div class="abs tt" style="left:24px;top:50px;color:var(--ink)">Content Here</div>
    <div class="abs tx" style="left:24px;top:62px;width:155px">Use this column for the main text of the slide. Keep each line short and clear so the point is easy to follow. Add a second sentence to give more detail and a third one to close the thought with care.</div>
    <div class="abs tt b" style="left:204px;top:50px">Content Here</div>
    <div class="abs tx" style="left:204px;top:62px;width:155px">Use this column for the main text of the slide. Keep each line short and clear so the point is easy to follow. Add a second sentence to give more detail and a third one to close the thought with care.</div>
    <div class="foot"><span>HOLLOWAY ENGINES | 2021</span><span>PAGE | 8</span></div>
  </article>

  <article class="slide">
    <div class="head">Your Title Here - Three Column</div>
    <div class="mark">HOLLOWAY<br>ENGINES</div>
    <div class="abs tt" style="left:14px;top:50px;color:var(--ink)">Content Here</div>
    <div class="abs tx" style="left:14px;top:62px;width:106px">Use this column for the main text of the slide. Keep each line short and clear so the point is easy to follow. Add a second sentence to give more detail and a third one to close the thought.</div>
    <div class="abs tt b" style="left:136px;top:50px">Content Here</div>
    <div class="abs tx" style="left:136px;top:62px;width:106px">Use this column for the main text of the slide. Keep each line short and clear so the point is easy to follow. Add a second sentence to give more detail and a third one to close the thought.</div>
    <div class="abs tt" style="left:258px;top:50px;color:var(--ink)">Content Here</div>
    <div class="abs tx" style="left:258px;top:62px;width:106px">Use this column for the main text of the slide. Keep each line short and clear so the point is easy to follow. Add a second sentence to give more detail and a third one to close the thought.</div>
    <div class="foot"><span>HOLLOWAY ENGINES | 2021</span><span>PAGE | 9</span></div>
  </article>

  <article class="slide">
    <div class="head">Your Title Here - <em>with foot notes</em></div>
    <div class="sub">Subtitle Goes Here</div>
    <div class="mark">HOLLOWAY<br>ENGINES</div>
    <div class="abs tx" style="left:14px;top:46px;width:120px;display:flex;gap:4px"><span class="dot" style="flex:none;background:var(--blue);margin-top:1px"></span><span>Add a short line of text here to explain this point, with a little more detail on the trend shown in the chart.</span></div>
    <div class="abs tx" style="left:14px;top:94px;width:120px;display:flex;gap:4px"><span class="dot" style="flex:none;background:var(--blue);margin-top:1px"></span><span>Add a short line of text here to explain this point, with a little more detail on the trend shown in the chart.</span></div>
    <svg class="abs" style="left:142px;top:40px" width="225" height="124" viewBox="0 0 225 124">
      <g stroke="var(--line)" stroke-width=".6"><line x1="18" y1="10" x2="220" y2="10"/><line x1="18" y1="35" x2="220" y2="35"/><line x1="18" y1="60" x2="220" y2="60"/><line x1="18" y1="85" x2="220" y2="85"/><line x1="18" y1="110" x2="220" y2="110"/></g>
      <polyline fill="none" stroke="var(--blue)" stroke-width="1.3" points="18,100 30,96 45,98 60,90 75,86 90,88 105,78 120,74 135,70 150,62 165,58 180,50 195,40 210,30 220,22"/>
      <g font-size="4.6" fill="var(--grey)" font-family="Montserrat"><text x="0" y="12">100</text><text x="0" y="37">75</text><text x="0" y="62">50</text><text x="0" y="87">25</text><text x="0" y="112">0</text>
      <text x="40" y="120">2016</text><text x="95" y="120">2017</text><text x="150" y="120">2018</text><text x="200" y="120">2019</text></g>
    </svg>
    <div class="abs" style="left:14px;right:14px;top:170px;border-top:1px solid var(--line);padding-top:3px;font-size:4.2px;color:var(--body)">Source: internal data. Figures are shown for guidance only and may change without notice.</div>
    <div class="foot"><span>HOLLOWAY ENGINES | 2021</span><span>PAGE | 10</span></div>
  </article>

  <article class="slide">
    <div class="head">Bullets Points</div>
    <div class="mark">HOLLOWAY<br>ENGINES</div>
    <div class="abs" style="left:28px;top:44px;display:grid;grid-template-columns:160px 160px;row-gap:11px;column-gap:20px">
      <div style="display:flex;gap:6px"><svg width="16" height="16" style="flex:none"><circle cx="8" cy="8" r="8" fill="var(--navy)"/><text x="8" y="10.5" text-anchor="middle" font-size="7" fill="#fff" font-weight="700" font-family="Montserrat">1</text></svg><div><div class="tt" style="color:var(--ink)">Content Title here</div><div class="tx">Add a short line of text here to explain this point.</div></div></div>
      <div style="display:flex;gap:6px"><svg width="16" height="16" style="flex:none"><circle cx="8" cy="8" r="8" fill="var(--navy)"/><text x="8" y="10.5" text-anchor="middle" font-size="7" fill="#fff" font-weight="700" font-family="Montserrat">4</text></svg><div><div class="tt" style="color:var(--ink)">Content Title here</div><div class="tx">Add a short line of text here to explain this point.</div></div></div>
      <div style="display:flex;gap:6px"><svg width="16" height="16" style="flex:none"><circle cx="8" cy="8" r="8" fill="var(--sky)"/><text x="8" y="10.5" text-anchor="middle" font-size="7" fill="#fff" font-weight="700" font-family="Montserrat">2</text></svg><div><div class="tt b">Content Title here</div><div class="tx">Add a short line of text here to explain this point.</div></div></div>
      <div style="display:flex;gap:6px"><svg width="16" height="16" style="flex:none"><circle cx="8" cy="8" r="8" fill="var(--sky)"/><text x="8" y="10.5" text-anchor="middle" font-size="7" fill="#fff" font-weight="700" font-family="Montserrat">5</text></svg><div><div class="tt b">Content Title here</div><div class="tx">Add a short line of text here to explain this point.</div></div></div>
      <div style="display:flex;gap:6px"><svg width="16" height="16" style="flex:none"><circle cx="8" cy="8" r="8" fill="var(--line)"/><text x="8" y="10.5" text-anchor="middle" font-size="7" fill="var(--grey)" font-weight="700" font-family="Montserrat">3</text></svg><div><div class="tt" style="color:var(--grey)">Content Title here</div><div class="tx">Add a short line of text here to explain this point.</div></div></div>
      <div style="display:flex;gap:6px"><svg width="16" height="16" style="flex:none"><circle cx="8" cy="8" r="8" fill="var(--line)"/><text x="8" y="10.5" text-anchor="middle" font-size="7" fill="var(--grey)" font-weight="700" font-family="Montserrat">6</text></svg><div><div class="tt" style="color:var(--grey)">Content Title here</div><div class="tx">Add a short line of text here to explain this point.</div></div></div>
    </div>
    <div class="foot"><span>HOLLOWAY ENGINES | 2021</span><span>PAGE | 11</span></div>
  </article>

  <article class="slide">
    <div class="head">Your Title Here</div>
    <div class="sub">Subtitle Goes Here</div>
    <div class="mark">HOLLOWAY<br>ENGINES</div>
    <div class="abs tt" style="left:14px;top:48px;color:var(--ink)">Content Here</div>
    <div class="abs tx" style="left:14px;top:60px;width:150px">Use this column for the main text of the slide. Keep each line short and clear so the point is easy to follow. Add a second sentence to give more detail and a third one to close the thought with care.</div>
    <div class="abs photo desk" role="img" aria-label="Laptop with code on a desk" style="left:186px;top:50px;width:180px;height:112px"></div>
    <svg class="abs" style="left:172px;top:62px" width="28" height="90"><circle cx="14" cy="14" r="11" fill="var(--navy)" stroke="#fff" stroke-width="2"/><circle cx="14" cy="45" r="11" fill="var(--sky)" stroke="#fff" stroke-width="2"/><circle cx="14" cy="76" r="11" fill="var(--grey)" stroke="#fff" stroke-width="2"/></svg>
    <div class="foot"><span>HOLLOWAY ENGINES | 2021</span><span>PAGE | 12</span></div>
  </article>

  <article class="slide">
    <div class="head">CEO DIRECTOR</div>
    <div class="sub">Holloway Engines Presentation</div>
    <div class="mark">HOLLOWAY<br>ENGINES</div>
    <div class="abs photo" role="img" aria-label="Portrait of the director" style="left:36px;top:50px;width:84px;height:82px"></div>
    <div class="abs tt" style="left:36px;top:138px;width:84px;text-align:center;color:var(--ink)">NAME HERE</div>
    <svg class="abs" style="left:62px;top:150px" width="32" height="8"><circle cx="4" cy="4" r="3.5" fill="var(--navy)"/><circle cx="16" cy="4" r="3.5" fill="var(--navy)"/><circle cx="28" cy="4" r="3.5" fill="var(--navy)"/></svg>
    <div class="abs tt" style="left:150px;top:50px;color:var(--ink)">Content Here</div>
    <div class="abs tx" style="left:150px;top:61px;width:95px">Add a short line of text here to explain this point in more detail.</div>
    <div class="abs tt b" style="left:258px;top:50px">Content Here</div>
    <div class="abs tx" style="left:258px;top:61px;width:95px">Add a short line of text here to explain this point in more detail.</div>
    <div class="abs" style="left:150px;top:112px;width:196px;height:6px;background:var(--line)"><div style="width:90%;height:100%;background:var(--navy)"></div></div>
    <div class="abs" style="left:150px;top:124px;width:196px;height:6px;background:var(--line)"><div style="width:75%;height:100%;background:var(--sky)"></div></div>
    <div class="abs tx" style="left:350px;top:111px">90%</div><div class="abs tx" style="left:350px;top:123px">75%</div>
    <div class="abs tx" style="left:280px;top:150px">hello@hollowayengines.com</div>
    <div class="foot"><span>HOLLOWAY ENGINES | 2021</span><span>PAGE | 13</span></div>
  </article>

  <article class="slide">
    <div class="head">Our Team</div>
    <div class="mark">HOLLOWAY<br>ENGINES</div>
    <div class="abs" style="left:26px;top:42px;display:grid;grid-template-columns:repeat(4,74px);column-gap:10px;text-align:center">
      <div><div class="photo" role="img" aria-label="Team member portrait" style="height:60px"></div><div style="background:var(--navy);color:#fff;font-size:5px;font-weight:700;padding:2px">Member Name</div><div style="font-size:4.2px;letter-spacing:1px;color:var(--grey);margin:3px 0 1px">POSITION</div><div class="tx">Add a short line of text here.</div></div>
      <div><div class="photo warm" role="img" aria-label="Team member portrait" style="height:60px"></div><div style="background:var(--sky);color:#fff;font-size:5px;font-weight:700;padding:2px">Member Name</div><div style="font-size:4.2px;letter-spacing:1px;color:var(--grey);margin:3px 0 1px">POSITION</div><div class="tx">Add a short line of text here.</div></div>
      <div><div class="photo" role="img" aria-label="Team member portrait" style="height:60px"></div><div style="background:var(--navy);color:#fff;font-size:5px;font-weight:700;padding:2px">Member Name</div><div style="font-size:4.2px;letter-spacing:1px;color:var(--grey);margin:3px 0 1px">POSITION</div><div class="tx">Add a short line of text here.</div></div>
      <div><div class="photo warm" role="img" aria-label="Team member portrait" style="height:60px"></div><div style="background:var(--sky);color:#fff;font-size:5px;font-weight:700;padding:2px">Member Name</div><div style="font-size:4.2px;letter-spacing:1px;color:var(--grey);margin:3px 0 1px">POSITION</div><div class="tx">Add a short line of text here.</div></div>
    </div>
    <div class="foot"><span>HOLLOWAY ENGINES | 2021</span><span>PAGE | 14</span></div>
  </article>

  <article class="slide">
    <div class="head">Your Title Here</div>
    <div class="sub">Subtitle Goes Here</div>
    <div class="mark">HOLLOWAY<br>ENGINES</div>
    <div class="abs" style="left:24px;top:46px;display:grid;grid-template-columns:repeat(4,76px);column-gap:4px">
      <div style="border:1px solid var(--line);height:116px;position:relative;padding:5px"><div style="font-size:14px;font-weight:700;color:var(--navy)">01</div><div class="tx">Add a short line of text here to explain this option in more detail.</div><div style="position:absolute;left:0;right:0;bottom:0;background:var(--navy);color:#fff;font-size:5px;font-weight:700;padding:3px 5px">Option Name</div></div>
      <div style="border:1px solid var(--line);height:116px;position:relative;padding:5px"><div style="font-size:14px;font-weight:700;color:var(--blue)">02</div><div class="tx">Add a short line of text here to explain this option in more detail.</div><div style="position:absolute;left:0;right:0;bottom:0;background:var(--blue);color:#fff;font-size:5px;font-weight:700;padding:3px 5px">Option Name</div></div>
      <div style="border:1px solid var(--line);height:116px;position:relative;padding:5px"><div style="font-size:14px;font-weight:700;color:var(--sky)">03</div><div class="tx">Add a short line of text here to explain this option in more detail.</div><div style="position:absolute;left:0;right:0;bottom:0;background:var(--sky);color:#fff;font-size:5px;font-weight:700;padding:3px 5px">Option Name</div></div>
      <div style="border:1px solid var(--line);height:116px;position:relative;padding:5px"><div style="font-size:14px;font-weight:700;color:var(--ink)">04</div><div class="tx">Add a short line of text here to explain this option in more detail.</div><div style="position:absolute;left:0;right:0;bottom:0;background:var(--pale);color:var(--navy);font-size:5px;font-weight:700;padding:3px 5px">Option Name</div></div>
    </div>
    <div class="foot"><span>HOLLOWAY ENGINES | 2021</span><span>PAGE | 15</span></div>
  </article>

  <article class="slide">
    <div class="head">Your Title Here - Infographic</div>
    <div class="mark">HOLLOWAY<br>ENGINES</div>
    <svg class="abs" style="left:30px;top:40px" width="140" height="140" viewBox="0 0 140 140">
      <circle cx="60" cy="70" r="40" fill="none" stroke="var(--line)" stroke-width="1.5"/>
      <circle cx="60" cy="70" r="30" fill="#fff" stroke="var(--line)"/>
      <circle cx="100" cy="70" r="8" fill="var(--sky)"/><circle cx="88" cy="40" r="8" fill="var(--navy)"/><circle cx="88" cy="100" r="8" fill="var(--pale)"/><circle cx="60" cy="30" r="4" fill="var(--navy)"/><circle cx="60" cy="110" r="4" fill="var(--grey)"/>
      <text x="60" y="68" text-anchor="middle" font-size="6" font-weight="800" fill="var(--navy)" font-family="Montserrat">HOLLOWAY</text>
      <text x="60" y="76" text-anchor="middle" font-size="6" font-weight="800" fill="var(--navy)" font-family="Montserrat">ENGINES</text>
    </svg>
    <div class="abs stack" style="left:186px;top:44px;width:175px;gap:8px">
      <div style="display:flex;gap:5px"><svg width="10" height="10" style="flex:none"><circle cx="5" cy="5" r="5" fill="var(--navy)"/><path d="M2.5 5l1.8 1.8L7.5 3.5" stroke="#fff" fill="none"/></svg><div><div class="tt" style="color:var(--ink)">Content Title</div><div class="tx">Add a short line of text here to explain this point.</div></div></div>
      <div style="display:flex;gap:5px"><svg width="10" height="10" style="flex:none"><circle cx="5" cy="5" r="5" fill="var(--sky)"/><path d="M2.5 5l1.8 1.8L7.5 3.5" stroke="#fff" fill="none"/></svg><div><div class="tt b">Content Title</div><div class="tx">Add a short line of text here to explain this point.</div></div></div>
      <div style="display:flex;gap:5px"><svg width="10" height="10" style="flex:none"><circle cx="5" cy="5" r="5" fill="var(--pale)"/><path d="M2.5 5l1.8 1.8L7.5 3.5" stroke="#fff" fill="none"/></svg><div><div class="tt" style="color:var(--ink)">Content Title</div><div class="tx">Add a short line of text here to explain this point.</div></div></div>
      <div style="display:flex;gap:5px"><svg width="10" height="10" style="flex:none"><circle cx="5" cy="5" r="5" fill="var(--grey)"/><path d="M2.5 5l1.8 1.8L7.5 3.5" stroke="#fff" fill="none"/></svg><div><div class="tt" style="color:var(--ink)">Content Title</div><div class="tx">Add a short line of text here to explain this point.</div></div></div>
    </div>
    <div class="foot"><span>HOLLOWAY ENGINES | 2021</span><span>PAGE | 16</span></div>
  </article>

  <article class="slide">
    <div class="head">Pie Charts</div>
    <div class="mark">HOLLOWAY<br>ENGINES</div>
    <div class="abs tx" style="left:70px;top:38px;width:240px;text-align:center">Add a short line of text here to explain the numbers below and what they mean for the reader.</div>
    <svg class="abs" style="left:30px;top:66px" width="320" height="60" viewBox="0 0 320 60">
      <g fill="none" stroke-width="5">
        <circle cx="60" cy="30" r="22" stroke="var(--line)"/><circle cx="60" cy="30" r="22" stroke="var(--navy)" stroke-dasharray="94 138" transform="rotate(-90 60 30)"/>
        <circle cx="160" cy="30" r="22" stroke="var(--line)"/><circle cx="160" cy="30" r="22" stroke="var(--sky)" stroke-dasharray="48 138" transform="rotate(-90 160 30)"/>
        <circle cx="260" cy="30" r="22" stroke="var(--line)"/><circle cx="260" cy="30" r="22" stroke="var(--pale)" stroke-dasharray="76 138" transform="rotate(-90 260 30)"/>
      </g>
      <g font-size="10" font-weight="700" text-anchor="middle" font-family="Montserrat"><text x="60" y="34" fill="var(--navy)">68%</text><text x="160" y="34" fill="var(--sky)">35%</text><text x="260" y="34" fill="var(--grey)">55%</text></g>
    </svg>
    <div class="abs tx" style="left:56px;top:134px;width:68px;text-align:center">Add a short line of text here.</div>
    <div class="abs tx" style="left:156px;top:134px;width:68px;text-align:center">Add a short line of text here.</div>
    <div class="abs tx" style="left:256px;top:134px;width:68px;text-align:center">Add a short line of text here.</div>
    <div class="foot"><span>HOLLOWAY ENGINES | 2021</span><span>PAGE | 17</span></div>
  </article>

  <article class="slide">
    <div class="head">Infographic Style</div>
    <div class="mark">HOLLOWAY<br>ENGINES</div>
    <div class="abs" style="left:30px;top:50px;width:112px;height:96px;border:1px solid var(--line)"></div>
    <svg class="abs" style="left:24px;top:44px" width="16" height="16"><circle cx="8" cy="8" r="8" fill="var(--navy)"/><text x="8" y="11" text-anchor="middle" font-size="9" fill="#fff" font-weight="700" font-family="Montserrat">$</text></svg>
    <div class="abs" style="left:42px;top:54px;font-size:34px;font-weight:700;color:var(--navy)">08</div>
    <div class="abs" style="left:98px;top:74px;background:var(--navy);color:#fff;font-size:4.5px;font-weight:700;padding:2px 5px">COST</div>
    <div class="abs" style="left:54px;top:98px;font-size:10px;font-weight:700;color:var(--navy)">Million</div>
    <div class="abs tx" style="left:38px;top:114px;width:96px;text-align:center">Add a short line of text here to explain it.</div>
    <div class="abs" style="left:180px;top:42px;font-size:30px;font-weight:700;color:var(--sky)">04</div>
    <div class="abs" style="left:230px;top:52px;background:var(--sky);color:#fff;font-size:4.5px;font-weight:700;padding:2px 5px">SALES</div>
    <div class="abs" style="left:230px;top:64px;font-size:8px;font-weight:700;color:var(--sky)">Million</div>
    <div class="abs tx" style="left:282px;top:50px;width:80px">Add a short line of text here to explain it.</div>
    <div class="abs" style="left:180px;top:104px;font-size:30px;font-weight:700;color:var(--line)">15</div>
    <div class="abs" style="left:224px;top:122px;font-size:5px;font-weight:700;color:var(--grey)">PERCENTAGE</div>
    <div class="abs tx" style="left:282px;top:114px;width:80px">Add a short line of text here to explain it.</div>
    <div class="foot"><span>HOLLOWAY ENGINES | 2021</span><span>PAGE | 18</span></div>
  </article>

  <article class="slide dark">
    <div class="mark" style="left:0;right:0;top:30px;color:var(--white);font-size:9px">HOLLOWAY<br>ENGINES</div>
    <div class="abs" style="left:24px;top:138px;font-size:28px;font-weight:700;color:var(--white)">01</div>
    <div class="abs" style="left:80px;top:144px;font-size:12px;font-weight:700;color:var(--white)">SECTION TITLE</div>
    <div class="abs" style="left:80px;top:162px;font-size:4.6px;color:var(--pale)">Add a short line of text here to introduce this section of the talk.</div>
  </article>

  <article class="slide">
    <div class="mark" style="left:0;right:0;top:30px;font-size:9px;color:#16202c">HOLLOWAY<br>ENGINES</div>
    <div class="abs" style="left:24px;top:138px;font-size:28px;font-weight:700;color:var(--ink)">02</div>
    <div class="abs" style="left:80px;top:144px;font-size:12px;font-weight:700;color:var(--ink)">SECTION TITLE</div>
    <div class="abs" style="left:80px;top:162px;font-size:4.6px;color:var(--body)">Add a short line of text here to introduce this section of the talk.</div>
  </article>

  <article class="slide">
    <div class="head">Infographic Style</div>
    <div class="mark">HOLLOWAY<br>ENGINES</div>
    <svg class="abs" style="left:140px;top:40px" width="100" height="130" viewBox="0 0 100 130">
      <g transform="translate(50 65)" stroke="#fff" stroke-width="2">
        <path d="M0 0 L0 -45 A45 45 0 0 1 31.8 -31.8Z" fill="var(--navy)"/>
        <path d="M0 0 L31.8 -31.8 A45 45 0 0 1 45 0Z" fill="var(--blue)"/>
        <path d="M0 0 L45 0 A45 45 0 0 1 31.8 31.8Z" fill="var(--sky)"/>
        <path d="M0 0 L31.8 31.8 A45 45 0 0 1 0 45Z" fill="var(--navy)"/>
        <path d="M0 0 L0 45 A45 45 0 0 1 -31.8 31.8Z" fill="var(--pale)"/>
        <path d="M0 0 L-31.8 31.8 A45 45 0 0 1 -45 0Z" fill="var(--blue)"/>
        <path d="M0 0 L-45 0 A45 45 0 0 1 -31.8 -31.8Z" fill="var(--sky)"/>
        <path d="M0 0 L-31.8 -31.8 A45 45 0 0 1 0 -45Z" fill="var(--pale)"/>
        <circle r="18" fill="#fff"/>
      </g>
    </svg>
    <div class="abs stack" style="left:20px;top:44px;width:114px;text-align:right;gap:7px">
      <div><div class="tt" style="color:var(--ink)">Content Title</div><div class="tx">Add a short line of text here.</div></div>
      <div><div class="tt b">Content Title</div><div class="tx">Add a short line of text here.</div></div>
      <div><div class="tt" style="color:var(--sky)">Content Title</div><div class="tx">Add a short line of text here.</div></div>
      <div><div class="tt" style="color:var(--ink)">Content Title</div><div class="tx">Add a short line of text here.</div></div>
    </div>
    <div class="abs stack" style="left:248px;top:44px;width:114px;gap:7px">
      <div><div class="tt" style="color:var(--ink)">Content Title</div><div class="tx">Add a short line of text here.</div></div>
      <div><div class="tt b">Content Title</div><div class="tx">Add a short line of text here.</div></div>
      <div><div class="tt" style="color:var(--sky)">Content Title</div><div class="tx">Add a short line of text here.</div></div>
      <div><div class="tt" style="color:var(--ink)">Content Title</div><div class="tx">Add a short line of text here.</div></div>
    </div>
    <div class="foot"><span>HOLLOWAY ENGINES | 2021</span><span>PAGE | 19</span></div>
  </article>

  <article class="slide">
    <div class="head">SWOT Analysis</div>
    <div class="mark">HOLLOWAY<br>ENGINES</div>
    <svg class="abs" style="left:150px;top:52px" width="80" height="110" viewBox="0 0 80 110">
      <circle cx="40" cy="30" r="16" fill="#fff" stroke="var(--navy)" stroke-width="3"/>
      <circle cx="62" cy="52" r="16" fill="#fff" stroke="var(--sky)" stroke-width="3"/>
      <circle cx="40" cy="74" r="16" fill="#fff" stroke="var(--grey)" stroke-width="3"/>
      <circle cx="18" cy="52" r="16" fill="#fff" stroke="var(--pale)" stroke-width="3"/>
      <g font-size="9" font-weight="700" text-anchor="middle" font-family="Montserrat"><text x="40" y="33" fill="var(--navy)">S</text><text x="62" y="55" fill="var(--sky)">W</text><text x="40" y="77" fill="var(--grey)">O</text><text x="18" y="55" fill="var(--pale)">T</text></g>
    </svg>
    <div class="abs" style="left:26px;top:50px;width:118px;text-align:right"><div class="tt" style="color:var(--ink)">Strength</div><div class="tx">Add a short line of text here to explain this point.</div></div>
    <div class="abs" style="left:26px;top:112px;width:118px;text-align:right"><div class="tt" style="color:var(--grey)">Threat</div><div class="tx">Add a short line of text here to explain this point.</div></div>
    <div class="abs" style="left:238px;top:50px;width:118px"><div class="tt b">Weakness</div><div class="tx">Add a short line of text here to explain this point.</div></div>
    <div class="abs" style="left:238px;top:112px;width:118px"><div class="tt" style="color:var(--ink)">Opportunity</div><div class="tx">Add a short line of text here to explain this point.</div></div>
    <div class="foot"><span>HOLLOWAY ENGINES | 2021</span><span>PAGE | 20</span></div>
  </article>

  <article class="slide">
    <div class="head">Our Structure</div>
    <div class="mark">HOLLOWAY<br>ENGINES</div>
    <svg class="abs" style="left:30px;top:38px" width="140" height="140" viewBox="0 0 140 140">
      <g fill="none" stroke-width="14" transform="rotate(-90 70 70)">
        <circle cx="70" cy="70" r="48" stroke="var(--navy)" stroke-dasharray="150.8 301.6"/>
        <circle cx="70" cy="70" r="48" stroke="var(--sky)" stroke-dasharray="90.5 301.6" stroke-dashoffset="-150.8"/>
        <circle cx="70" cy="70" r="48" stroke="var(--pale)" stroke-dasharray="30.2 301.6" stroke-dashoffset="-241.3"/>
        <circle cx="70" cy="70" r="48" stroke="var(--line)" stroke-dasharray="30.2 301.6" stroke-dashoffset="-271.5"/>
      </g>
      <g font-size="6" font-weight="700" fill="#fff" font-family="Montserrat"><text x="16" y="74">50%</text><text x="106" y="58">30%</text><text x="98" y="114">10%</text><text x="46" y="25" fill="var(--grey)">10%</text></g>
      <text x="70" y="68" text-anchor="middle" font-size="6" font-weight="800" fill="var(--navy)" font-family="Montserrat">HOLLOWAY</text>
      <text x="70" y="76" text-anchor="middle" font-size="6" font-weight="800" fill="var(--navy)" font-family="Montserrat">ENGINES</text>
    </svg>
    <div class="abs stack" style="left:200px;top:48px;width:160px;gap:10px">
      <div class="tx" style="border-left:2px solid var(--navy);padding-left:5px">Add a short line of text here to explain this share.</div>
      <div class="tx" style="border-left:2px solid var(--sky);padding-left:5px">Add a short line of text here to explain this share.</div>
      <div class="tx" style="border-left:2px solid var(--pale);padding-left:5px">Add a short line of text here to explain this share.</div>
      <div class="tx" style="border-left:2px solid var(--line);padding-left:5px">Add a short line of text here to explain this share.</div>
    </div>
    <div class="foot"><span>HOLLOWAY ENGINES | 2021</span><span>PAGE | 21</span></div>
  </article>

  <article class="slide">
    <div class="head">Chart with Text</div>
    <div class="mark">HOLLOWAY<br>ENGINES</div>
    <svg class="abs" style="left:14px;top:38px" width="210" height="140" viewBox="0 0 210 140">
      <text x="105" y="10" text-anchor="middle" font-size="5.5" fill="var(--ink)" font-family="Montserrat">Series 1</text>
      <g font-size="4.6" fill="var(--grey)" font-family="Montserrat"><text x="0" y="32">6</text><text x="0" y="62">4</text><text x="0" y="92">2</text><text x="0" y="122">0</text></g>
      <line x1="10" y1="120" x2="205" y2="120" stroke="var(--line)"/>
      <g fill="var(--navy)">
        <rect x="20" y="70" width="5" height="50"/><rect x="38" y="90" width="5" height="30"/><rect x="56" y="50" width="5" height="70"/><rect x="74" y="80" width="5" height="40"/><rect x="92" y="40" width="5" height="80"/><rect x="110" y="66" width="5" height="54"/><rect x="128" y="56" width="5" height="64"/><rect x="146" y="84" width="5" height="36"/><rect x="164" y="30" width="5" height="90"/><rect x="182" y="60" width="5" height="60"/>
      </g>
      <g fill="var(--sky)"><rect x="26" y="96" width="5" height="24"/><rect x="62" y="86" width="5" height="34"/><rect x="98" y="92" width="5" height="28"/><rect x="134" y="98" width="5" height="22"/><rect x="170" y="80" width="5" height="40"/></g>
      <g font-size="4.6" fill="var(--grey)" font-family="Montserrat" text-anchor="middle"><text x="25" y="128">2011</text><text x="61" y="128">2013</text><text x="97" y="128">2015</text><text x="133" y="128">2017</text><text x="169" y="128">2019</text><text x="105" y="137">— Series 1   — Series 2</text></g>
    </svg>
    <div class="abs" style="left:238px;top:46px;width:126px;height:116px;border:1px solid var(--line);padding:7px">
      <div style="background:var(--navy);color:#fff;font-size:5px;font-weight:700;padding:2px 4px;display:inline-block">Content 01</div>
      <div class="tx" style="margin-top:5px">Add a short line of text here to explain the chart and the trend it shows over time.</div>
      <div class="tx" style="margin-top:4px">Add a second line of text with one more detail for the reader.</div>
      <div style="font-size:4.6px;font-weight:700;color:var(--navy);margin-top:8px;text-align:center">ADD YOUR TEXT HERE</div>
    </div>
    <div class="foot"><span>HOLLOWAY ENGINES | 2021</span><span>PAGE | 22</span></div>
  </article>

  <article class="slide">
    <div class="head">Table Chart - Option 01</div>
    <div class="mark">HOLLOWAY<br>ENGINES</div>
    <table class="abs" style="left:30px;top:44px;width:320px;border-collapse:collapse;font-size:4.8px;text-align:center;color:var(--body)">
      <tr style="background:var(--navy);color:#fff;font-weight:700;height:13px"><td style="width:24px;background:#fff"></td><td>TEXT HERE</td><td>TEXT HERE</td><td>TEXT HERE</td></tr>
      <tr style="height:21px;background:var(--mist)"><td><svg width="9" height="9"><circle cx="4.5" cy="4.5" r="4.5" fill="var(--navy)"/></svg></td><td>Add Content Here</td><td>Add Content Here</td><td>Add Content Here</td></tr>
      <tr style="height:21px"><td><svg width="9" height="9"><circle cx="4.5" cy="4.5" r="4.5" fill="var(--navy)"/></svg></td><td>Add Content Here</td><td>Add Content Here</td><td>Add Content Here</td></tr>
      <tr style="height:21px;background:var(--mist)"><td><svg width="9" height="9"><circle cx="4.5" cy="4.5" r="4.5" fill="var(--navy)"/></svg></td><td>Add Content Here</td><td>Add Content Here</td><td>Add Content Here</td></tr>
      <tr style="height:21px"><td><svg width="9" height="9"><circle cx="4.5" cy="4.5" r="4.5" fill="var(--navy)"/></svg></td><td>Add Content Here</td><td>Add Content Here</td><td>Add Content Here</td></tr>
      <tr style="height:21px;background:var(--mist)"><td><svg width="9" height="9"><circle cx="4.5" cy="4.5" r="4.5" fill="var(--navy)"/></svg></td><td>Add Content Here</td><td>Add Content Here</td><td>Add Content Here</td></tr>
    </table>
    <div class="foot"><span>HOLLOWAY ENGINES | 2021</span><span>PAGE | 23</span></div>
  </article>

  <article class="slide">
    <div class="head">Bar Chart</div>
    <div class="sub">Subtitle Goes Here</div>
    <div class="mark">HOLLOWAY<br>ENGINES</div>
    <div class="abs tx" style="left:60px;top:36px;width:260px;text-align:center">Add a short line of text here to explain the chart below.</div>
    <svg class="abs" style="left:14px;top:52px" width="350" height="118" viewBox="0 0 350 118">
      <g font-size="4.6" fill="var(--grey)" font-family="Montserrat"><text x="0" y="8">100%</text><text x="0" y="33">75%</text><text x="0" y="58">50%</text><text x="0" y="83">25%</text><text x="0" y="106">0%</text></g>
      <g fill="var(--line)"><rect x="40" y="6" width="12" height="98"/><rect x="75" y="6" width="12" height="98"/><rect x="110" y="6" width="12" height="98"/><rect x="145" y="6" width="12" height="98"/><rect x="180" y="6" width="12" height="98"/><rect x="215" y="6" width="12" height="98"/><rect x="250" y="6" width="12" height="98"/><rect x="285" y="6" width="12" height="98"/><rect x="320" y="6" width="12" height="98"/></g>
      <rect x="40" y="70" width="12" height="34" fill="var(--navy)"/><rect x="75" y="64" width="12" height="40" fill="var(--pale)"/><rect x="110" y="76" width="12" height="28" fill="var(--navy)"/><rect x="145" y="62" width="12" height="42" fill="var(--sky)"/><rect x="180" y="54" width="12" height="50" fill="var(--navy)"/><rect x="215" y="58" width="12" height="46" fill="var(--pale)"/><rect x="250" y="50" width="12" height="54" fill="var(--navy)"/><rect x="285" y="60" width="12" height="44" fill="var(--sky)"/><rect x="320" y="46" width="12" height="58" fill="var(--navy)"/>
      <g font-size="4.6" fill="var(--grey)" font-family="Montserrat" text-anchor="middle"><text x="46" y="113">2011</text><text x="81" y="113">2012</text><text x="116" y="113">2013</text><text x="151" y="113">2014</text><text x="186" y="113">2015</text><text x="221" y="113">2016</text><text x="256" y="113">2017</text><text x="291" y="113">2018</text><text x="326" y="113">2019</text></g>
    </svg>
    <div class="foot"><span>HOLLOWAY ENGINES | 2021</span><span>PAGE | 24</span></div>
  </article>

  <article class="slide">
    <div class="head">Logos with Text</div>
    <div class="mark">HOLLOWAY<br>ENGINES</div>
    <div class="abs" style="left:24px;top:50px;display:grid;grid-template-columns:repeat(3,44px);gap:8px">
      <div style="height:24px;border:1px solid var(--line);display:flex;align-items:center;justify-content:center"><span style="width:10px;height:10px;background:var(--pale)"></span></div>
      <div style="height:24px;border:1px solid var(--line);display:flex;align-items:center;justify-content:center"><span style="width:10px;height:10px;background:var(--pale)"></span></div>
      <div style="height:24px;border:1px solid var(--line);display:flex;align-items:center;justify-content:center"><span style="width:10px;height:10px;background:var(--pale)"></span></div>
      <div style="height:24px;border:1px solid var(--line);display:flex;align-items:center;justify-content:center"><span style="width:10px;height:10px;background:var(--pale)"></span></div>
      <div style="height:24px;border:1px solid var(--line);display:flex;align-items:center;justify-content:center"><span style="width:10px;height:10px;background:var(--pale)"></span></div>
      <div style="height:24px;border:1px solid var(--line);display:flex;align-items:center;justify-content:center"><span style="width:10px;height:10px;background:var(--pale)"></span></div>
      <div style="height:24px;border:1px solid var(--line);display:flex;align-items:center;justify-content:center"><span style="width:10px;height:10px;background:var(--pale)"></span></div>
      <div style="height:24px;border:1px solid var(--line);display:flex;align-items:center;justify-content:center"><span style="width:10px;height:10px;background:var(--pale)"></span></div>
      <div style="height:24px;border:1px solid var(--line);display:flex;align-items:center;justify-content:center;font-size:4.4px;color:var(--grey);text-align:center">Add Client Logo</div>
    </div>
    <div class="abs" style="left:214px;top:52px;width:118px"><div class="tt" style="color:var(--ink)">Contents Title</div><div class="tx">Add a short line of text here to explain this point.</div></div>
    <div class="abs" style="left:214px;top:104px;width:118px"><div class="tt b">Contents Title</div><div class="tx">Add a short line of text here to explain this point.</div></div>
    <svg class="abs" style="left:342px;top:50px" width="16" height="70"><circle cx="8" cy="8" r="7" fill="var(--navy)"/><text x="8" y="10" text-anchor="middle" font-size="5" fill="#fff" font-weight="700" font-family="Montserrat">01</text><circle cx="8" cy="60" r="7" fill="var(--sky)"/><text x="8" y="62" text-anchor="middle" font-size="5" fill="#fff" font-weight="700" font-family="Montserrat">02</text></svg>
    <div class="foot"><span>HOLLOWAY ENGINES | 2021</span><span>PAGE | 25</span></div>
  </article>

  <article class="slide">
    <div class="abs photo warm" role="img" aria-label="Hand signing a document" style="left:0;top:0;width:186px;height:146px"></div>
    <div class="abs" style="left:110px;top:14px;font-size:12px;font-weight:700;color:var(--white)">Case Study</div>
    <div class="abs" style="left:0;top:146px;width:186px;height:66px;background:var(--white);padding:12px 12px 0 14px">
      <div class="tx" style="color:var(--ink)">Add a short quote here from the client about the result of the work.</div>
      <div class="tx" style="text-align:right;margin-top:4px;color:var(--ink);font-weight:600">Name Here</div>
    </div>
    <svg class="abs" style="left:10px;top:134px" width="22" height="22"><circle cx="11" cy="11" r="10" fill="var(--navy)"/><text x="11" y="20" text-anchor="middle" font-size="16" fill="#fff" font-weight="800" font-family="Montserrat">“</text></svg>
    <div class="mark">HOLLOWAY<br>ENGINES</div>
    <div class="abs stack" style="left:204px;top:48px;width:160px;gap:10px">
      <div style="display:flex;gap:5px"><svg width="12" height="12" style="flex:none"><circle cx="6" cy="6" r="6" fill="var(--navy)"/></svg><div><div class="tt" style="color:var(--ink)">Challenge</div><div class="tx">Add a short line of text here to explain this point.</div></div></div>
      <div style="display:flex;gap:5px"><svg width="12" height="12" style="flex:none"><circle cx="6" cy="6" r="6" fill="var(--sky)"/></svg><div><div class="tt b">Solution</div><div class="tx">Add a short line of text here to explain this point.</div></div></div>
      <div style="display:flex;gap:5px"><svg width="12" height="12" style="flex:none"><circle cx="6" cy="6" r="6" fill="var(--pale)"/></svg><div><div class="tt" style="color:var(--grey)">Result</div><div class="tx">Add a short line of text here to explain this point.</div></div></div>
    </div>
    <div class="foot" style="left:200px"><span>HOLLOWAY ENGINES | 2021</span><span>PAGE | 26</span></div>
  </article>

  <article class="slide">
    <div class="head">Disclaimer</div>
    <div class="mark">HOLLOWAY<br>ENGINES</div>
    <div class="abs stack" style="left:14px;top:38px;width:351px;gap:4px">
      <p class="tx" style="font-size:4.2px;line-height:1.4">This material is for information only and does not form an offer to buy or sell any product. Past results are no guide to future returns, and the value of any holding can fall as well as rise. Figures shown are drawn from sources we believe are sound but we give no promise as to their accuracy or that they are complete. Nothing here should be read as advice on tax, law or investment.</p>
      <p class="tx" style="font-size:4.2px;line-height:1.4">The views set out reflect our thinking at the date shown and may change without notice. Models and back tests carry limits and may not reflect real trading costs or market impact. Any forecast is an estimate and may not come true. Readers should seek their own advice before they act on any part of this document.</p>
      <p class="tx" style="font-size:4.2px;line-height:1.4">This document is meant only for the person to whom it is given and may not be passed on, copied or shared in whole or in part without prior written consent. It is not meant for use in any place where its use would break local law or rules. Some products named here may not be open to all types of investor.</p>
      <p class="tx" style="font-size:4.2px;line-height:1.4">Holloway Engines holds no duty to update this material. All rights are reserved. For more detail on risk, terms and fees, please ask your contact for the full set of fund papers and read them with care before you make any choice to invest with us.</p>
    </div>
    <div class="foot"><span>HOLLOWAY ENGINES | 2021</span><span>PAGE | 27</span></div>
  </article>

  <article class="slide">
    <div class="head">Free Icons</div>
    <div class="mark">HOLLOWAY<br>ENGINES</div>
    <svg class="abs" style="left:20px;top:40px" width="340" height="140" viewBox="0 0 340 140">
      <defs><pattern id="iconGrid" width="17" height="17" patternUnits="userSpaceOnUse"><circle cx="8" cy="8" r="4" fill="none" stroke="var(--grey)" stroke-width=".8"/></pattern></defs>
      <rect width="340" height="136" fill="url(#iconGrid)"/>
    </svg>
    <div class="foot"><span>HOLLOWAY ENGINES | 2021</span><span>PAGE | 28</span></div>
  </article>

  <article class="slide dark">
    <div class="abs" style="left:34px;top:32px;font-size:13px;font-weight:700;color:var(--white)">THANK YOU</div>
    <div class="abs" style="left:34px;top:64px;font-size:5.5px;font-weight:700;color:var(--white);letter-spacing:.05em">PRESENTER NAME</div>
    <div class="abs stack" style="left:34px;top:84px;gap:7px;font-size:4.8px;color:var(--white)">
      <div style="display:flex;gap:5px;align-items:center"><svg width="8" height="8" viewBox="0 0 8 8"><path d="M1.5 1h1.5l.8 1.8-1 .7a4 4 0 0 0 1.7 1.7l.7-1 1.8.8v1.5c-3.5 0-6-2.5-6-5z" fill="#fff"/></svg>+1 000 555 0199</div>
      <div style="display:flex;gap:5px;align-items:center"><svg width="8" height="8"><circle cx="4" cy="4" r="3.4" fill="none" stroke="#fff"/></svg>www.hollowayengines.com</div>
      <div style="display:flex;gap:5px;align-items:center"><svg width="8" height="8"><rect x=".5" y="1.5" width="7" height="5" fill="none" stroke="#fff"/><path d="M.5 1.5l3.5 3 3.5-3" fill="none" stroke="#fff"/></svg>hello@hollowayengines.com</div>
      <div style="display:flex;gap:5px;align-items:center"><svg width="8" height="8"><path d="M4 7.5S1.5 4.8 1.5 3.2a2.5 2.5 0 0 1 5 0C6.5 4.8 4 7.5 4 7.5z" fill="#fff"/></svg>Add your location here</div>
    </div>
    <div class="brand md on-dark abs" style="left:200px;top:116px;width:150px">Holloway<br>Engines</div>
    <div class="abs" style="left:0;right:0;bottom:10px;text-align:center;font-size:4.2px;color:var(--pale)">Add a short closing line of text here.</div>
  </article>

  <article class="slide">
    <div class="abs" style="left:34px;top:32px;font-size:13px;font-weight:700;color:var(--navy)">THANK YOU</div>
    <div class="abs" style="left:34px;top:64px;font-size:5.5px;font-weight:700;color:var(--ink);letter-spacing:.05em">PRESENTER NAME</div>
    <div class="abs stack" style="left:34px;top:84px;gap:7px;font-size:4.8px;color:var(--ink)">
      <div style="display:flex;gap:5px;align-items:center"><svg width="8" height="8" viewBox="0 0 8 8"><path d="M1.5 1h1.5l.8 1.8-1 .7a4 4 0 0 0 1.7 1.7l.7-1 1.8.8v1.5c-3.5 0-6-2.5-6-5z" fill="var(--navy)"/></svg>+1 000 555 0199</div>
      <div style="display:flex;gap:5px;align-items:center"><svg width="8" height="8"><circle cx="4" cy="4" r="3.4" fill="none" stroke="var(--navy)"/></svg>www.hollowayengines.com</div>
      <div style="display:flex;gap:5px;align-items:center"><svg width="8" height="8"><rect x=".5" y="1.5" width="7" height="5" fill="none" stroke="var(--navy)"/><path d="M.5 1.5l3.5 3 3.5-3" fill="none" stroke="var(--navy)"/></svg>hello@hollowayengines.com</div>
      <div style="display:flex;gap:5px;align-items:center"><svg width="8" height="8"><path d="M4 7.5S1.5 4.8 1.5 3.2a2.5 2.5 0 0 1 5 0C6.5 4.8 4 7.5 4 7.5z" fill="var(--navy)"/></svg>Add your location here</div>
    </div>
    <div class="brand md abs" style="left:200px;top:100px;width:150px;color:#16202c">Holloway<br>Engines</div>
  </article>

</main>
</body>
</html>
```